New Business Card Design Project LORVANTI-Italy

we are LORVANTI-Italy
our company in the market for 3 years we are luxury cosmetic company and its about time for a facelift :)
i will like to have elegant luxurious and unique business card
that will give the person that get it a unique, luxurious and elegant impression
I'm VERY OPEN FOR NEW IDEAS , even duo i add a few files of things that i see on line and i like them

i add my logo as well
my website is LORVANTI.COM
(if you would like to see the main style that we have)

Target Market(s)

adult that have money :)

Industry/Entity Type

Business

Contact Information for Business Card

Name - Dario Lorvanti
Position - CEO and CO Founder
address - 4817 E Halvern
telephone - 555-384-1926
email - dario@lorvanti.com
fax - 555-384-1926
website - LORVANTI.COM

Colors
000000
959595
fbee3e
ffffff

Requirements
Must have
• big logo in GOLD color
• elegant look
• impressive
Nice to have
• not must but maybe classy pattern background
• not must but maybe emblem
• maybe clear plastic business card
Should not have
• colors
• images

```html
<!DOCTYPE html>
<html lang="en">
<head>
<meta charset="utf-8">
<title>LORVANTI Italy – Business Card</title>
<link rel="stylesheet" href="https://fonts.googleapis.com/css2?family=Cinzel:wght@400;700&family=Open+Sans:wght@400;600&display=swap">
<style>
  :root {
    --black: #000000;
    --white: #ffffff;
    --gold-light: #e6d072;
    --gold: #d4b34a;
    --gold-deep: #c9a63c;
    --grey: #959595;
  }
  * { margin: 0; padding: 0; box-sizing: border-box; }
  html, body { width: 1200px; height: 900px; overflow: hidden; background: var(--white); }
  .stage { position: relative; width: 1200px; height: 900px; }
  .card {
    position: absolute; top: 271px; width: 458px; height: 282px;
    background: var(--black); border-radius: 12px; overflow: hidden;
    box-shadow: 1px 3px 4px rgba(0,0,0,0.35);
  }
  .card--front { left: 137px; }
  .card--back { left: 626px; }

  .gold-band {
    position: absolute; left: 343px; top: 0; width: 115px; height: 100%;
    background: var(--white);
  }
  .gold-band::after {
    content: ""; position: absolute; left: 12px; top: 0; right: 0; bottom: 0;
    background: linear-gradient(160deg, var(--gold-light), var(--gold-deep));
  }
  .seal {
    position: absolute; left: 271px; top: 61px; width: 156px; height: 156px;
    border-radius: 50%; background: var(--white);
    display: flex; align-items: center; justify-content: center;
  }
  .seal__name {
    font-family: "Cinzel", serif; font-weight: 700; font-size: 17px;
    color: var(--gold-deep); letter-spacing: 1px;
  }

  .holder { position: absolute; left: 36px; top: 53px; }
  .holder__name {
    font-family: "Cinzel", serif; font-weight: 700; font-size: 21px;
    color: var(--gold-light); letter-spacing: 0.5px; line-height: 1.2;
  }
  .holder__role {
    font-family: "Open Sans", sans-serif; font-size: 13px; color: var(--white); margin-top: 1px;
  }
  .contacts { list-style: none; position: absolute; left: 36px; top: 117px; }
  .contacts li {
    display: flex; align-items: center; height: 22.5px;
    font-family: "Open Sans", sans-serif; font-size: 13px; color: var(--white);
  }
  .contacts svg { width: 16px; height: 16px; margin-right: 6px; flex: none; }
  .address {
    position: absolute; left: 36px; top: 219px;
    font-family: "Open Sans", sans-serif; font-size: 13px; color: var(--white);
  }

  .brand { position: absolute; left: 0; width: 100%; text-align: center; }
  .brand__ring {
    position: absolute; left: 179px; top: 41px; width: 100px; height: 100px;
    border-radius: 50%; border: 3px solid var(--gold);
  }
  .brand__name {
    top: 158px; font-family: "Cinzel", serif; font-weight: 400; font-size: 40px;
    color: var(--gold); letter-spacing: 1px; line-height: 1;
  }
  .brand__rule {
    position: absolute; left: 118px; top: 213px; width: 222px; height: 2px;
    background: var(--gold);
  }
  .brand__place {
    top: 222px; font-family: "Cinzel", serif; font-size: 16px;
    color: var(--gold); letter-spacing: 1px;
  }
</style>
</head>
<body>
<div class="stage">
  <section class="card card--front">
    <div class="gold-band"></div>
    <div class="seal"><span class="seal__name">LORVANTI</span></div>

    <div class="holder">
      <h1 class="holder__name">DARIO LORVANTI</h1>
      <p class="holder__role">CEO and CO Founder</p>
    </div>

    <ul class="contacts">
      <li>
        <svg viewBox="0 0 16 16"><circle cx="8" cy="8" r="8" fill="#ffffff"/><path d="M4.5 6.5c0-1.2 1.6-2 3.5-2s3.5.8 3.5 2l-1.5.5-.5-1H6.5l-.5 1zM5.5 8h5l.8 3.5H4.7z" fill="#d4b34a"/></svg>
        555-384-1926
      </li>
      <li>
        <svg viewBox="0 0 16 16"><circle cx="8" cy="8" r="8" fill="#ffffff"/><rect x="5" y="4" width="6" height="8" rx="1" fill="#d4b34a"/><rect x="6" y="5" width="4" height="3" fill="#ffffff"/></svg>
        555-384-1926
      </li>
      <li>
        <svg viewBox="0 0 16 16"><circle cx="8" cy="8" r="8" fill="#ffffff"/><rect x="4" y="5" width="8" height="6" fill="#d4b34a"/><path d="M4 5l4 3.3L12 5" fill="none" stroke="#ffffff" stroke-width="0.9"/></svg>
        dario@lorvanti.com
      </li>
      <li>
        <svg viewBox="0 0 16 16"><circle cx="8" cy="8" r="8" fill="#ffffff"/><circle cx="8" cy="8" r="4" fill="none" stroke="#d4b34a" stroke-width="1.4"/><path d="M4 8h8M8 4v8" stroke="#d4b34a" stroke-width="1"/></svg>
        WWW.LORVANTI.COM
      </li>
    </ul>

    <p class="address">4817 E Halvern</p>
  </section>

  <section class="card card--back">
    <div class="brand__ring"></div>
    <p class="brand brand__name">LORVANTI</p>
    <div class="brand__rule"></div>
    <p class="brand brand__place">ITALY</p>
  </section>
</div>
</body>
</html>
```